We are looking for Facebook and Instagram templates. To use both platforms we will use square images. We need a template for our posts, not the header image.
Most posts contain multiple images and we need a designoverlay in which we can embed our images.
Attached a screenshot of our website www.talurepo.be, our logo in svg and ai. The monkey is our mascotte (excact this monkey, not another).
We offer teambuildings, the style should be fun. Colors are antracite, limegreen and white. I did attache the current layout for posts but we are not happy with this.
If we could have some small design elements (like stickers) we can always create a new layout but is feels the same.
Our website is quite simple, this should also be in these post designs. Simple forms, rounded corners.
Updates

Allow more time for the designers, good work requires more time

Target Market(s)

Teambuilding

Industry/Entity Type

Teambuilding

Font styles to use
Other font styles liked:
• RobotoSlab

Requirements
Must have
• If we could have some small design elements (like stickers) we can always create a new layout but is feels the same.
Should not have
• Complex design, simple images works best for us

```html
<!DOCTYPE html>
<html lang="nl">
<head>
<meta charset="utf-8">
<title>Talurepo – social post templates</title>
<link href="https://fonts.googleapis.com/css2?family=Barlow+Condensed:wght@400;500;600;700;800&display=swap" rel="stylesheet">
<style>
:root{
  --antracite:#2b2c2e;
  --antracite-soft:#3a3b3e;
  --lime:#a5c615;
  --lime-dark:#8aa80f;
  --white:#ffffff;
  --ink:#1f2022;
}
*{box-sizing:border-box;margin:0;padding:0}
html,body{width:1200px;height:813px;overflow:hidden;background:var(--white)}
body{position:relative;font-family:"Barlow Condensed",sans-serif;color:var(--white)}
.icon-defs{position:absolute;width:0;height:0}

.post{position:absolute;width:359px;height:359px;background:var(--antracite);overflow:hidden}
.post--a{left:33px;top:34px}
.post--b{left:420px;top:34px}
.post--c{left:808px;top:34px}
.post--d{left:33px;top:420px}
.post--e{left:420px;top:420px}
.post--f{left:808px;top:420px}

.abs{position:absolute}

/* brand plate */
.brand{position:absolute;border:1.5px solid #d9d9d9;background:var(--antracite-soft);text-align:center;line-height:1}
.brand__name{display:block;font-weight:800;color:var(--white);letter-spacing:.5px}
.brand__sub{display:block;background:#4a4b4e;color:#e6e6e6;font-weight:500;letter-spacing:1px}

/* photos */
.photo{position:absolute;background:linear-gradient(135deg,#5c6b46,#3d4a35 55%,#7b6a5a)}
.photo--indoor{background:linear-gradient(135deg,#2e3f7a,#5a3a6a 60%,#7a4a3a)}
.photo--group{background:linear-gradient(135deg,#3a3230,#6a5a50 55%,#2a2a2a)}
.photo--forest{background:linear-gradient(160deg,#47663a,#2f4a2c 50%,#8a7a5a)}
.photo--grass{background:linear-gradient(160deg,#6f8a4a,#4a6a35 60%,#a8b08a)}
.frame{position:absolute;background:var(--white);border-radius:5px;box-shadow:0 2px 5px rgba(0,0,0,.35)}

.title{position:absolute;font-weight:800;line-height:1;text-transform:uppercase}
.rule{position:absolute;height:1px;background:var(--lime)}
.copy{position:absolute;font-weight:400;line-height:1.45}

/* pillars */
.pillar{position:absolute;display:flex;align-items:center;gap:6px;font-weight:700;text-transform:uppercase}
.pillar__icon{flex:none;border-radius:50%;display:flex;align-items:center;justify-content:center}
.pillar__icon svg{width:70%;height:70%}
.pillar--dark .pillar__icon{background:var(--antracite);color:var(--lime)}
.pillar--lime .pillar__icon{background:var(--lime);color:var(--antracite)}
.pillar--dark{color:var(--antracite)}

.divider{position:absolute;background:rgba(255,255,255,.25)}

/* footer */
.footer{position:absolute;left:0;width:359px;display:flex;justify-content:space-between;align-items:center;padding:0 20px 0 20px}
.footer__addr{display:flex;align-items:center;gap:8px;font-size:10.5px;line-height:1.2}
.footer__url{display:flex;align-items:center;gap:4px;font-size:11px}
.pin,.globe{width:10px;height:10px;flex:none}

.brush{position:absolute;background:var(--lime);clip-path:polygon(2% 18%,14% 10%,30% 14%,48% 4%,66% 10%,84% 2%,100% 8%,98% 32%,100% 60%,96% 88%,78% 94%,58% 90%,40% 98%,22% 92%,6% 100%,0 76%,3% 48%)}
.spark{position:absolute;stroke:var(--lime);stroke-width:1.5;stroke-linecap:round;fill:none}
.pushpin{position:absolute;width:7px;height:7px;border-radius:50%;background:#e0262a;box-shadow:0 1px 2px rgba(0,0,0,.5)}
</style>
</head>
<body>

<svg class="icon-defs" aria-hidden="true">
  <symbol id="i-target" viewBox="0 0 24 24"><g fill="none" stroke="currentColor" stroke-width="1.6"><circle cx="12" cy="12" r="8"/><circle cx="12" cy="12" r="4"/><path d="M12 1v6M12 17v6M1 12h6M17 12h6"/></g></symbol>
  <symbol id="i-bulb" viewBox="0 0 24 24"><g fill="none" stroke="currentColor" stroke-width="1.6"><path d="M8 14a6 6 0 1 1 8 0c-1 1-1.5 2-1.5 3h-5c0-1-.5-2-1.5-3z"/><path d="M9.5 20h5M10 22.5h4M12 2V0M4 9H2M22 9h-2"/></g></symbol>
  <symbol id="i-team" viewBox="0 0 24 24"><g fill="none" stroke="currentColor" stroke-width="1.6"><circle cx="12" cy="8" r="3"/><circle cx="5" cy="10" r="2.3"/><circle cx="19" cy="10" r="2.3"/><path d="M6.5 19a5.5 5.5 0 0 1 11 0zM1 18a4 4 0 0 1 5-3.5M23 18a4 4 0 0 0-5-3.5"/></g></symbol>
  <symbol id="i-pin" viewBox="0 0 24 24"><path fill="currentColor" d="M12 1a8 8 0 0 0-8 8c0 6 8 14 8 14s8-8 8-14a8 8 0 0 0-8-8zm0 11a3 3 0 1 1 0-6 3 3 0 0 1 0 6z"/></symbol>
  <symbol id="i-globe" viewBox="0 0 24 24"><g fill="none" stroke="currentColor" stroke-width="1.8"><circle cx="12" cy="12" r="10"/><ellipse cx="12" cy="12" rx="4.5" ry="10"/><path d="M2 12h20M4 6.5h16M4 17.5h16"/></g></symbol>
</svg>

<!-- Post A -->
<section class="post post--a">
  <div class="brand" style="left:20px;top:21px;width:71px;height:26px">
    <span class="brand__name" style="font-size:12px;padding-top:2px">TALUREPO</span>
    <span class="brand__sub" style="font-size:6px;padding:1px 0;margin-top:2px">DE HAVEN</span>
  </div>
  <svg class="spark" style="left:84px;top:54px" width="16" height="16" viewBox="0 0 16 16"><path d="M4 10 2 2M8 10l6-5M9 13h6"/></svg>
  <h2 class="title" style="left:20px;top:66px;font-size:28px">Inzet<br>bouwverlof</h2>
  <div class="rule" style="left:20px;top:133px;width:82px"></div>
  <p class="copy" style="left:20px;top:143px;font-size:13px;line-height:1.3">Full house met de inzet van<br>de zomervakantie</p>
  <div class="frame" style="left:187px;top:20px;width:157px;height:186px;transform:rotate(-3deg)">
    <div class="photo photo--forest" role="img" aria-label="Groep in kilts juicht met vlaggen in het bos" style="left:5px;top:5px;right:5px;bottom:5px;border-radius:3px"></div>
  </div>
  <div class="abs" style="left:-4px;top:204px;width:370px;height:68px;background:var(--lime);transform:rotate(-2deg)"></div>
  <div class="pillar pillar--dark" style="left:22px;top:220px;font-size:11px"><span class="pillar__icon" style="width:24px;height:24px"><svg><use href="#i-target"/></svg></span>Uitdagen</div>
  <div class="abs" style="left:115px;top:218px;width:1px;height:30px;background:rgba(0,0,0,.2)"></div>
  <div class="pillar pillar--dark" style="left:136px;top:220px;font-size:11px"><span class="pillar__icon" style="width:24px;height:24px"><svg><use href="#i-bulb"/></svg></span>Inspireren</div>
  <div class="abs" style="left:238px;top:218px;width:1px;height:30px;background:rgba(0,0,0,.2)"></div>
  <div class="pillar pillar--dark" style="left:257px;top:220px;font-size:11px"><span class="pillar__icon" style="width:24px;height:24px"><svg><use href="#i-team"/></svg></span>Verbinden</div>
  <div class="frame" style="left:18px;top:266px;width:100px;height:62px;transform:rotate(-3deg)"><div class="photo photo--indoor" role="img" aria-label="Team speelt een escape-spel" style="left:4px;top:4px;right:4px;bottom:4px"></div></div>
  <div class="pushpin" style="left:62px;top:258px"></div>
  <div class="frame" style="left:128px;top:254px;width:98px;height:66px;transform:rotate(2deg)"><div class="photo photo--indoor" role="img" aria-label="Deelnemers springen in een neonruimte" style="left:4px;top:4px;right:4px;bottom:4px"></div></div>
  <div class="pushpin" style="left:175px;top:247px"></div>
  <div class="frame" style="left:235px;top:258px;width:102px;height:64px;transform:rotate(-4deg)"><div class="photo photo--indoor" role="img" aria-label="Collega's spelen een arcadespel" style="left:4px;top:4px;right:4px;bottom:4px"></div></div>
  <div class="pushpin" style="left:277px;top:249px"></div>
  <svg class="spark" style="left:116px;top:318px" width="16" height="20" viewBox="0 0 16 20"><path d="M14 2 6 4M13 8 5 14M6 18 4 10"/></svg>
  <div class="footer__url abs" style="right:20px;top:325px;color:var(--lime);font-size:14px"><svg class="globe" style="width:11px;height:11px"><use href="#i-globe"/></svg>www.talurepo.be</div>
</section>

<!-- Post B -->
<section class="post post--b">
  <div class="brush" style="left:22px;top:50px;width:316px;height:80px;transform:rotate(-5deg)"></div>
  <div class="brand" style="left:125px;top:26px;width:110px;height:40px">
    <span class="brand__name" style="font-size:19px;padding-top:4px">TALUREPO</span>
    <span class="brand__sub" style="font-size:9px;padding:1px 0;margin-top:3px">DE HAVEN</span>
  </div>
  <svg class="spark" style="left:92px;top:74px" width="18" height="16" viewBox="0 0 18 16"><path d="M2 9l8 4M8 3l4 7M15 1l-1 8" stroke="var(--antracite)"/></svg>
  <h2 class="title" style="left:60px;top:76px;font-size:19px;color:var(--antracite);text-align:center;transform:rotate(-5deg);line-height:1.05">Klaar om samen<br>herinneringen te maken?</h2>
  <div class="frame" style="left:25px;top:135px;width:103px;height:123px;transform:rotate(-3deg)"><div class="photo photo--indoor" role="img" aria-label="Deelnemers in een donkere spelruimte" style="left:6px;top:6px;right:6px;height:80px;border-radius:3px"></div><span class="abs" style="left:0;right:0;bottom:10px;text-align:center;color:var(--ink);font-weight:600;font-size:15px">Laser Dash!</span></div>
  <div class="frame" style="left:128px;top:132px;width:100px;height:123px;transform:rotate(2deg)"><div class="photo photo--group" role="img" aria-label="Workshop parfum maken aan tafel" style="left:6px;top:6px;right:6px;height:80px;border-radius:3px"></div><span class="abs" style="left:0;right:0;bottom:12px;text-align:center;color:var(--ink);font-weight:600;font-size:15px">Parfum maken</span></div>
  <div class="frame" style="left:230px;top:135px;width:104px;height:123px;transform:rotate(-4deg)"><div class="photo photo--forest" role="img" aria-label="Groep drumt buiten op het gras" style="left:6px;top:6px;right:6px;height:80px;border-radius:3px"></div><span class="abs" style="left:0;right:0;bottom:12px;text-align:center;color:var(--ink);font-weight:600;font-size:15px">Percussie</span></div>
  <svg class="spark" style="left:20px;top:264px" width="16" height="16" viewBox="0 0 16 16"><path d="M2 10h8M6 4l4 6M13 2v7"/></svg>
  <p class="copy" style="left:30px;top:276px;width:300px;text-align:center;font-size:9.5px">Lorem Ipsum is simply dummy text of the printing and typesetting industry korem Ipsum has been the industry's standard dummy text.</p>
  <div class="abs" style="left:0;top:314px;width:240px;height:32px;background:var(--lime)"></div>
  <div class="abs" style="left:240px;top:318px;width:119px;height:24px;background:var(--white)"></div>
  <div class="abs" style="left:0;top:346px;width:359px;height:13px;background:var(--antracite)"></div>
  <div class="footer__addr abs" style="left:20px;top:323px;color:var(--antracite);font-size:8.5px"><svg class="pin" style="color:var(--antracite)"><use href="#i-pin"/></svg>Brakelstraat 12, 3580 Verbeke, Belgium</div>
  <div class="footer__url abs" style="left:240px;top:322px;color:var(--antracite);font-size:12px"><svg class="globe" style="color:var(--antracite)"><use href="#i-globe"/></svg>www.talurepo.be</div>
</section>

<!-- Post C -->
<section class="post post--c">
  <div class="abs" style="left:20px;top:48px;width:326px;height:160px;background:var(--lime);border-radius:14px;transform:rotate(-1.5deg)"></div>
  <div class="photo photo--group" role="img" aria-label="Groep collega's steekt duimen omhoog" style="left:18px;top:52px;width:320px;height:148px;border:3px solid var(--white);border-radius:12px;transform:rotate(-1deg)"></div>
  <div class="brand" style="left:118px;top:22px;width:115px;height:42px">
    <span class="brand__name" style="font-size:20px;padding-top:4px">TALUREPO</span>
    <span class="brand__sub" style="font-size:10px;padding:1px 0;margin-top:3px">DE HAVEN</span>
  </div>
  <div class="pillar pillar--lime" style="left:21px;top:234px;font-size:11.5px"><span class="pillar__icon" style="width:25px;height:25px"><svg><use href="#i-target"/></svg></span>Uitdagen</div>
  <div class="divider" style="left:113px;top:234px;width:1px;height:24px"></div>
  <div class="pillar pillar--lime" style="left:131px;top:234px;font-size:11.5px"><span class="pillar__icon" style="width:25px;height:25px"><svg><use href="#i-bulb"/></svg></span>Inspireren</div>
  <div class="divider" style="left:236px;top:234px;width:1px;height:24px"></div>
  <div class="pillar pillar--lime" style="left:257px;top:234px;font-size:11.5px"><span class="pillar__icon" style="width:25px;height:25px"><svg><use href="#i-team"/></svg></span>Verbinden</div>
  <p class="copy" style="left:18px;top:276px;width:322px;text-align:center;font-size:9.5px">Lorem Ipsum is simply dummy text of the printing and typesetting industry korem Ipsum has been the industry's standard dummy text.</p>
  <div class="footer" style="top:322px;height:37px;background:var(--lime);color:var(--antracite);clip-path:polygon(0 10%,100% 0,100% 100%,0 100%)">
    <div class="footer__addr"><svg class="pin"><use href="#i-pin"/></svg><span>Brakelstraat 12, 3580<br>Verbeke, Belgium</span></div>
    <div class="footer__url"><svg class="globe"><use href="#i-globe"/></svg>www.talurepo.be</div>
  </div>
</section>

<!-- Post D -->
<section class="post post--d">
  <div class="abs" style="left:0;top:0;width:194px;height:292px;background:var(--white);border-bottom-right-radius:16px"></div>
  <div class="photo photo--forest" role="img" aria-label="Collega's doen een touwspel in het bos" style="left:0;top:0;width:188px;height:284px;border-bottom-right-radius:14px;border-right:2px solid var(--lime)"></div>
  <div class="brand" style="left:215px;top:21px;width:100px;height:35px">
    <span class="brand__name" style="font-size:17px;padding-top:3px">TALUREPO</span>
    <span class="brand__sub" style="font-size:8px;padding:1px 0;margin-top:3px">DE HAVEN</span>
  </div>
  <svg class="spark" style="left:266px;top:68px" width="16" height="16" viewBox="0 0 16 16"><path d="M3 10 2 2M7 10l7-5M9 13h6"/></svg>
  <h2 class="title" style="left:214px;top:80px;font-size:22px;line-height:1.1">Inzet<br>bouwverlof</h2>
  <div class="rule" style="left:214px;top:137px;width:122px"></div>
  <p class="copy" style="left:214px;top:147px;width:132px;font-size:5.6px">Lorem Ipsum is simply dummy text of the printing and typesetting industry korem Ipsum has been the industry's standard dummy text.</p>
  <div class="pillar pillar--lime" style="left:215px;top:185px;font-size:9.5px"><span class="pillar__icon" style="width:23px;height:23px"><svg><use href="#i-target"/></svg></span>Uitdagen</div>
  <div class="pillar pillar--lime" style="left:215px;top:220px;font-size:9.5px"><span class="pillar__icon" style="width:23px;height:23px"><svg><use href="#i-bulb"/></svg></span>Inspireren</div>
  <div class="pillar pillar--lime" style="left:215px;top:254px;font-size:9.5px"><span class="pillar__icon" style="width:23px;height:23px"><svg><use href="#i-team"/></svg></span>Verbinden</div>
  <div class="footer" style="top:316px;height:32px;background:var(--lime);color:var(--antracite)">
    <div class="footer__addr"><svg class="pin"><use href="#i-pin"/></svg><span>Brakelstraat 12, 3580<br>Verbeke, Belgium</span></div>
    <div class="footer__url"><svg class="globe"><use href="#i-globe"/></svg>www.talurepo.be</div>
  </div>
</section>

<!-- Post E -->
<section class="post post--e">
  <div class="brand" style="left:20px;top:21px;width:100px;height:35px">
    <span class="brand__name" style="font-size:17px;padding-top:3px">TALUREPO</span>
    <span class="brand__sub" style="font-size:8px;padding:1px 0;margin-top:3px">DE HAVEN</span>
  </div>
  <svg class="spark" style="left:134px;top:56px" width="16" height="16" viewBox="0 0 16 16"><path d="M3 10 4 2M7 10l7-5M9 13h6"/></svg>
  <h2 class="title" style="left:24px;top:72px;font-size:18px;transform:rotate(-5deg)">Teambuilding</h2>
  <div class="brush" style="left:12px;top:92px;width:158px;height:36px;transform:rotate(-5deg)"></div>
  <h2 class="title" style="left:34px;top:96px;font-size:23px;color:var(--antracite);transform:rotate(-5deg)">Met impact</h2>
  <p class="copy" style="left:20px;top:143px;width:155px;font-size:7.3px">Lorem Ipsum is simply dummy text of the printing and typesetting industry korem Ipsum has been the industry's standard dummy text.</p>
  <div class="pillar pillar--lime" style="left:20px;top:188px;font-size:9.5px"><span class="pillar__icon" style="width:23px;height:23px"><svg><use href="#i-target"/></svg></span>Uitdagen</div>
  <div class="divider" style="left:20px;top:218px;width:130px;height:1px"></div>
  <div class="pillar pillar--lime" style="left:20px;top:227px;font-size:9.5px"><span class="pillar__icon" style="width:23px;height:23px"><svg><use href="#i-bulb"/></svg></span>Inspireren</div>
  <div class="divider" style="left:20px;top:257px;width:130px;height:1px"></div>
  <div class="pillar pillar--lime" style="left:20px;top:266px;font-size:9.5px"><span class="pillar__icon" style="width:23px;height:23px"><svg><use href="#i-team"/></svg></span>Verbinden</div>
  <div class="frame" style="left:182px;top:55px;width:168px;height:178px;transform:rotate(-3deg)"><div class="photo photo--forest" role="img" aria-label="Collega's spelen lasergame in het bos" style="left:6px;top:6px;right:6px;bottom:6px;border-radius:4px;border:1.5px solid var(--lime)"></div></div>
  <div class="pushpin" style="left:254px;top:51px"></div>
  <svg class="spark" style="left:180px;top:238px" width="24" height="20" viewBox="0 0 24 20"><path d="M2 6l8-3M12 8 10 18M18 8l2 9"/></svg>
  <div class="footer" style="top:316px;height:32px;background:var(--lime);color:var(--antracite)">
    <div class="footer__addr"><svg class="pin"><use href="#i-pin"/></svg><span>Brakelstraat 12, 3580<br>Verbeke, Belgium</span></div>
    <div class="footer__url"><svg class="globe"><use href="#i-globe"/></svg>www.talurepo.be</div>
  </div>
</section>

<!-- Post F -->
<section class="post post--f">
  <div class="abs" style="left:0;top:0;width:199px;height:359px;background:var(--lime)"></div>
  <div class="photo photo--grass" role="img" aria-label="Vrouw met helm zwaait aan een touw over het gras" style="left:21px;top:19px;width:178px;height:297px;border-top-left-radius:14px"></div>
  <div class="brand" style="left:215px;top:21px;width:103px;height:37px">
    <span class="brand__name" style="font-size:17px;padding-top:4px">TALUREPO</span>
    <span class="brand__sub" style="font-size:8px;padding:1px 0;margin-top:3px">DE HAVEN</span>
  </div>
  <svg class="spark" style="left:267px;top:68px" width="16" height="16" viewBox="0 0 16 16"><path d="M3 10 4 2M7 10l7-5M9 13h6"/></svg>
  <h2 class="title" style="left:215px;top:76px;font-size:22px;line-height:1.1">Inzet<br>bouwverlof</h2>
  <p class="copy" style="left:215px;top:141px;width:132px;font-size:5.6px">Lorem Ipsum is simply dummy text of the printing and typesetting industry korem Ipsum has been the industry's standard dummy text.</p>
  <div class="pillar pillar--lime" style="left:215px;top:180px;font-size:9.5px"><span class="pillar__icon" style="width:23px;height:23px"><svg><use href="#i-target"/></svg></span>Uitdagen</div>
  <div class="divider" style="left:215px;top:210px;width:85px;height:1px"></div>
  <div class="pillar pillar--lime" style="left:215px;top:221px;font-size:9.5px"><span class="pillar__icon" style="width:23px;height:23px"><svg><use href="#i-bulb"/></svg></span>Inspireren</div>
  <div class="divider" style="left:215px;top:251px;width:85px;height:1px"></div>
  <div class="pillar pillar--lime" style="left:215px;top:262px;font-size:9.5px"><span class="pillar__icon" style="width:23px;height:23px"><svg><use href="#i-team"/></svg></span>Verbinden</div>
  <div class="footer" style="top:316px;height:32px;background:var(--antracite);color:var(--white)">
    <div class="footer__addr"><svg class="pin"><use href="#i-pin"/></svg><span>Brakelstraat 12, 3580<br>Verbeke, Belgium</span></div>
    <div class="footer__url"><svg class="globe"><use href="#i-globe"/></svg>www.talurepo.be</div>
  </div>
</section>

</body>
</html>
```